Business Card Design for Vintage Jazz

I am a vintage jazz band leader in New York City. My groups play the music of the 1920s, 1930s and 1940s. My website is morvalquist.com for more info on what I do.

I am looking for a two sided business card design that has the look and feel of a really nice business card from the 1930s. I need to convey with the design that my work has that vintage kind of class and style, but also conveys that we are fun and entertaining.

Most importantly it should make a bold staement. If Hal Denbrook had a card, what would it have looked like? I want a card that I feel confident will make an impact and will let people know that my work is te the top that NYC has to offer in vintage jazz..

Note that I have only decided to avoid the "committed payment" option as I have not used this service before. Assuming that I get quality work I will select a design from those presented.

Target Market(s)

people who want to hire my band for events, media, and new fans of the band

Industry/Entity Type

Performing Art

Contact Information for Business Card

Definitely a matte finish, possibly a sort of old style of paper with that brown tint? definitely a thick card.

Requirements
Must have
• FRONT
• My name: Tobin Vashley
• What I do: Bandleader, Guitarist, Vocalist, Songwriter
• Contact Details: morvalquist.com tobin@morvalquist.com 646-555-0148
• BACK
• My Social Media Links:
• facebook.morvalquist.com
• twitter, instagram, linkedin: morvalquist
• I'm also including a photo image I would like to use. The photo's background is not needed, and to be honest isn't really desireable. Just looking to use the image of me.
Nice to have
• I'm attaching which could be used as is, omitted from the card, or altered maybe with text going around the outside of the circle or in some other way. It may need some clean up to the edges of the lettering as we only use it for the website thumbnail.
• If there's space I'd like to include the text "join our mailing list for a free song download: freesong.morvalquist.com" If not perhaps just "Download a Free Song at: freesong.morvalquist.com - something to this end.
Should not have
• anything cartoony. Don't think retro 90s's vision of the swing era, think actual swing era!
• anything modern. Got to look old school
• Try to avoid dark backgrounds. Since we often play in bars and clubs where it is dar, a d
• avoid script fonts.

```html
<!DOCTYPE html>
<html lang="en">
<head>
<meta charset="utf-8">
<title>Tobin Vashley – Business Card</title>
<link rel="stylesheet" href="https://fonts.googleapis.com/css2?family=Source+Sans+3:ital,wght@0,400;0,600;1,600&display=swap">
<style>
  :root {
    --stage: #000000;
    --paper: #efe4cc;
    --paper-deep: #e3d3b2;
    --ink: #2b2118;
    --ink-soft: #4a3b2c;
    --band: #3b2d21;
    --band-ink: #f3e9d2;
    --rule: #a48c66;
    --frame: #8c7450;
    --photo-top: #b9a581;
    --photo-bottom: #7d6a4f;
  }
  html, body {
    margin: 0;
    padding: 0;
    width: 1200px;
    height: 900px;
    overflow: hidden;
    background: var(--stage);
    font-family: "Source Sans 3", "Myriad Pro", Arial, sans-serif;
  }
  .canvas { position: relative; width: 1200px; height: 900px; }
  .card {
    position: absolute;
    top: 271px;
    width: 456px;
    height: 281px;
    border-radius: 12px;
    overflow: hidden;
    background: radial-gradient(ellipse at 50% 40%, var(--paper) 55%, var(--paper-deep) 100%);
    color: var(--ink);
  }
  .card--front { left: 137px; }
  .card--back { left: 627px; }

  .deco-frame {
    position: absolute;
    inset: 8px;
    border: 1px solid var(--frame);
    border-radius: 6px;
    pointer-events: none;
  }
  .deco-frame::after {
    content: "";
    position: absolute;
    inset: 3px;
    border: 1px solid var(--frame);
    border-radius: 4px;
    opacity: 0.6;
  }
  .card--front .deco-frame { bottom: 75px; }

  .portrait {
    position: absolute;
    left: 14px; top: 16px;
    width: 174px; height: 198px;
    border-radius: 4px 4px 0 0;
    background: linear-gradient(180deg, var(--photo-top), var(--photo-bottom));
  }
  .divider {
    position: absolute;
    width: 1px;
    background: var(--rule);
  }
  .card--front .divider { left: 196px; top: 74px; height: 120px; }
  .card--back .divider { left: 220px; top: 90px; height: 105px; }

  .name {
    position: absolute;
    left: 215px; top: 74px;
    margin: 0;
    font-size: 19px;
    font-weight: 600;
    letter-spacing: 0.1px;
    color: var(--ink);
  }
  .contact-list, .social-list {
    position: absolute;
    margin: 0; padding: 0;
    list-style: none;
    font-size: 13.5px;
    color: var(--ink-soft);
  }
  .contact-list { left: 215px; top: 118px; }
  .contact-list li { height: 16.5px; line-height: 16.5px; display: flex; align-items: center; }
  .contact-list svg { width: 10px; height: 10px; margin-right: 7px; fill: var(--ink); }

  .role-band {
    position: absolute;
    left: 0; bottom: 0;
    width: 100%; height: 67px;
    background: var(--band);
    display: flex; align-items: center; justify-content: center;
    color: var(--band-ink);
    font-size: 14.5px;
    font-style: italic;
    font-weight: 600;
  }
  .role-band::before {
    content: "";
    position: absolute;
    left: 0; right: 0; top: 4px;
    height: 1px;
    background: var(--rule);
  }

  .wordmark {
    position: absolute;
    left: 40px; top: 105px;
    width: 160px;
    text-align: center;
    font-size: 20px;
    font-weight: 600;
    line-height: 1.2;
    color: var(--ink);
  }
  .social-list { left: 268px; top: 106px; }
  .social-list li { height: 20.5px; line-height: 20.5px; display: flex; align-items: center; }
  .social-list .marker {
    width: 12px; height: 12px;
    margin-right: 5px;
    background: var(--ink);
    border-radius: 2px;
  }
</style>
</head>
<body>
<main class="canvas">
  <section class="card card--front" aria-label="Card front">
    <div class="portrait" role="img" aria-label="Sepia photo of the bandleader in a striped jacket tipping a straw boater hat"></div>
    <span class="deco-frame"></span>
    <span class="divider"></span>
    <h1 class="name">Tobin Vashley</h1>
    <ul class="contact-list">
      <li><svg viewBox="0 0 10 10"><path d="M2 0.5 L3.6 2.6 L2.8 3.6 Q4 6 6.4 7.2 L7.4 6.4 L9.5 8 L8.3 9.5 Q2.5 8.8 0.5 1.7 Z"/></svg>646-555-0148</li>
      <li><svg viewBox="0 0 10 10"><path d="M0.5 2.5 H9.5 V8 H0.5 Z"/></svg>tobin@morvalquist.com</li>
      <li><svg viewBox="0 0 10 10"><circle cx="5" cy="5" r="4.5"/></svg>morvalquist.com</li>
    </ul>
    <div class="role-band">Bandleader, Guitarist, Vocalist, Songwriter</div>
  </section>

  <section class="card card--back" aria-label="Card back">
    <span class="deco-frame"></span>
    <div class="wordmark">Tobin<br>Vashley</div>
    <span class="divider"></span>
    <ul class="social-list">
      <li><span class="marker"></span>morvalquist.com</li>
      <li><span class="marker"></span>morvalquist</li>
      <li><span class="marker"></span>morvalquist</li>
      <li><span class="marker"></span>morvalquist</li>
    </ul>
  </section>
</main>
</body>
</html>
```